Sol Tranquila Coaching Services

My info is
Marisel Duarte-Vannoni
marisel@soltranquilacoaching.com
soltranquilacoaching.com
555-314-7702

you can play with order of items. I've never had a letterhead before. Thank you!

```html
<!DOCTYPE html>
<html lang="en">
<head>
<meta charset="utf-8">
<title>Sol Tranquila Coaching Services — Stationery</title>
<link rel="stylesheet" href="https://fonts.googleapis.com/css2?family=Montserrat:wght@500&family=Oswald:wght@300;400&display=swap">
<style>
  :root {
    --bg: #e4e4e4;
    --paper: #ffffff;
    --orange: #f0741b;
    --orange-light: #f7961f;
    --orange-deep: #e65f0e;
    --red: #c0182f;
    --ink: #444444;
    --rule: #cfcfcf;
    --ghost: #f0f0f0;
    --ghost-line: #e6e6e6;
  }
  * { box-sizing: border-box; margin: 0; padding: 0; }
  html, body {
    width: 1200px; height: 900px; overflow: hidden;
    background: var(--bg);
  }
  .canvas { position: relative; width: 1200px; height: 900px; }

  /* brand lockup */
  .brand { display: flex; flex-direction: column; align-items: center; text-align: center;
           font-family: "Montserrat", sans-serif; font-weight: 500; color: var(--red); }
  .brand-dot { width: 46px; height: 46px; border-radius: 50%; background: var(--orange); margin-bottom: 8px; }
  .brand-name { font-size: 24px; line-height: 1.1; letter-spacing: 0.5px; }
  .brand-sub { font-size: 10.5px; letter-spacing: 2.6px; text-transform: uppercase; margin-top: 3px; }
  .brand--light { color: #ffffff; }
  .brand--light .brand-dot { background: #ffffff; }

  /* contact block */
  .contact { font-family: "Oswald", sans-serif; color: var(--ink); }
  .contact-name { color: var(--red); font-weight: 400; }
  .contact-list { list-style: none; }
  .contact-list li { display: flex; align-items: center; font-weight: 300; }
  .contact-list svg { flex: none; fill: none; stroke: var(--red); stroke-width: 1.6; }

  /* letterhead */
  .letterhead {
    position: absolute; left: 64px; top: 100px; width: 563px; height: 726px;
    background: var(--paper); overflow: hidden;
  }
  .letterhead .brand { position: absolute; left: 30px; top: 18px; width: 160px; }
  .letterhead .brand-name { font-size: 20px; }
  .letterhead .brand-sub { font-size: 9px; letter-spacing: 2px; }
  .letterhead .contact { position: absolute; left: 401px; top: 38px; }
  .letterhead .contact-name { font-size: 14px; margin-bottom: 7px; }
  .letterhead .contact-list li { font-size: 10.5px; height: 20px; }
  .letterhead .contact-list svg { width: 11px; height: 11px; margin-right: 7px; }
  .letterhead-mark {
    position: absolute; left: 287px; top: 393px; width: 350px; height: 350px; border-radius: 50%;
    background: var(--ghost); border: 5px solid var(--ghost-line);
  }
  .letterhead-band { position: absolute; left: 0; bottom: 0; width: 100%; height: 16px; background: var(--orange); }

  /* business cards */
  .card { position: absolute; left: 708px; width: 424px; height: 242px; border-radius: 13px; overflow: hidden; }
  .card--front {
    top: 196px;
    background: radial-gradient(ellipse at 50% 40%, var(--orange-light) 0%, var(--orange) 55%, var(--orange-deep) 100%);
    display: flex; align-items: center; justify-content: center;
  }
  .card--front .brand-dot { width: 74px; height: 74px; margin-bottom: 14px; }
  .card--front .brand-name { font-size: 34px; }
  .card--front .brand-sub { font-size: 13.5px; letter-spacing: 3.2px; margin-top: 5px; }

  .card--back { top: 494px; background: linear-gradient(180deg, #fbfbfb 0%, #ffffff 40%, #f3f3f3 100%); }
  .card--back .brand { position: absolute; left: 14px; top: 52px; width: 196px; }
  .card--back .brand-dot { width: 64px; height: 64px; margin-bottom: 10px; }
  .card--back .brand-name { font-size: 24px; }
  .card--back .brand-sub { font-size: 11px; letter-spacing: 2.6px; }
  .card-divider { position: absolute; left: 221px; top: 50px; width: 1px; height: 130px; background: var(--rule); }
  .card--back .contact { position: absolute; left: 240px; top: 54px; }
  .card--back .contact-name { font-size: 19px; margin-bottom: 18px; }
  .card--back .contact-list li { font-size: 12.5px; height: 25px; }
  .card--back .contact-list svg { width: 12px; height: 12px; margin-right: 10px; }
  .card-band { position: absolute; left: 0; bottom: 0; width: 100%; height: 14px; background: var(--orange); }
</style>
</head>
<body>
<main class="canvas">

  <section class="letterhead" aria-label="Letterhead">
    <div class="brand">
      <span class="brand-dot"></span>
      <span class="brand-name">Sol Tranquila</span>
      <span class="brand-sub">Coaching Services</span>
    </div>
    <div class="contact">
      <p class="contact-name">Marisel Duarte-Vannoni</p>
      <ul class="contact-list">
        <li><svg viewBox="0 0 12 12"><path d="M3 1.5l1.6 2.2-1 1.1c.7 1.4 1.6 2.3 3 3l1.1-1 2.2 1.6-.9 1.6C5.6 10 2 6.4 1.5 2.4z"/></svg>555-314-7702</li>
        <li><svg viewBox="0 0 12 12"><rect x="1" y="2.5" width="10" height="7"/><path d="M1 2.5l5 4 5-4"/></svg>marisel@soltranquilacoaching.com</li>
        <li><svg viewBox="0 0 12 12"><circle cx="6" cy="6" r="4.8"/><path d="M1.2 6h9.6M6 1.2c2.2 2.6 2.2 7 0 9.6M6 1.2c-2.2 2.6-2.2 7 0 9.6"/></svg>soltranquilacoaching.com</li>
      </ul>
    </div>
    <div class="letterhead-mark" aria-hidden="true"></div>
    <div class="letterhead-band"></div>
  </section>

  <section class="card card--front" aria-label="Business card front">
    <div class="brand brand--light">
      <span class="brand-dot"></span>
      <span class="brand-name">Sol Tranquila</span>
      <span class="brand-sub">Coaching Services</span>
    </div>
  </section>

  <section class="card card--back" aria-label="Business card back">
    <div class="brand">
      <span class="brand-dot"></span>
      <span class="brand-name">Sol Tranquila</span>
      <span class="brand-sub">Coaching Services</span>
    </div>
    <div class="card-divider"></div>
    <div class="contact">
      <p class="contact-name">Marisel Duarte-Vannoni</p>
      <ul class="contact-list">
        <li><svg viewBox="0 0 12 12"><path d="M3 1.5l1.6 2.2-1 1.1c.7 1.4 1.6 2.3 3 3l1.1-1 2.2 1.6-.9 1.6C5.6 10 2 6.4 1.5 2.4z"/></svg>555-314-7702</li>
        <li><svg viewBox="0 0 12 12"><rect x="1" y="2.5" width="10" height="7"/><path d="M1 2.5l5 4 5-4"/></svg>marisel@soltranquilacoaching.com</li>
        <li><svg viewBox="0 0 12 12"><circle cx="6" cy="6" r="4.8"/><path d="M1.2 6h9.6M6 1.2c2.2 2.6 2.2 7 0 9.6M6 1.2c-2.2 2.6-2.2 7 0 9.6"/></svg>www.soltranquilacoaching.com</li>
      </ul>
    </div>
    <div class="card-band"></div>
  </section>

</main>
</body>
</html>
```